Local fast-growing company in the service sector

We are looking for a modern business card design, which should also appear on our letterheads

Target Market(s)

Private and industrial sectors

Contact Information for Business Card

Vorname Name
Kellberger Str. 18
72418 Haldenbach
Tel.: 07146-839214-0
Name@agentur-kvtl.de

Colors
9d9d9d
919191
aaaaaa

Requirements
Must have
• The logo (file) in silver

```html
<!DOCTYPE html>
<html lang="de">
<head>
<meta charset="utf-8">
<title>KVTL Visitenkarte</title>
<link href="https://fonts.googleapis.com/css2?family=Michroma&family=Montserrat:wght@400;600;800&display=swap" rel="stylesheet">
<style>
  :root {
    --backdrop: #8d8d8d;
    --backdrop-deep: #6f6f6f;
    --card: #2b2b2c;
    --card-light: #363637;
    --silver: #aaaaaa;
    --silver-mid: #9d9d9d;
    --silver-dark: #919191;
    --white: #f4f4f4;
  }
  * { margin: 0; padding: 0; box-sizing: border-box; }
  html, body { width: 799px; height: 1200px; overflow: hidden; }
  body {
    background: linear-gradient(135deg, var(--backdrop-deep), var(--backdrop));
    font-family: "Montserrat", sans-serif;
    position: relative;
  }
  .card {
    position: absolute;
    left: 89px;
    width: 620px;
    height: 354px;
    background: radial-gradient(ellipse at 55% 40%, var(--card-light), var(--card) 75%);
    box-shadow: 0 14px 30px rgba(0,0,0,0.45);
  }
  .card--front { top: 150px; }
  .card--back { top: 696px; }

  .front-brand {
    position: absolute;
    left: 50%;
    top: 50%;
    transform: translate(-50%, -50%);
    display: flex;
    flex-direction: column;
    align-items: flex-start;
  }
  .brand-row { display: flex; align-items: center; gap: 18px; }
  .brand-mark {
    width: 60px; height: 60px;
    background: var(--silver);
  }
  .brand-name {
    font-weight: 800;
    font-size: 88px;
    line-height: 0.9;
    letter-spacing: 2px;
    color: var(--silver);
  }
  .brand-web {
    margin-top: 10px;
    color: var(--silver);
    font-weight: 600;
    font-size: 26px;
    letter-spacing: 1px;
  }

  .back-brand {
    position: absolute;
    left: 54px;
    top: 104px;
    font-weight: 800;
    font-size: 60px;
    line-height: 1;
    color: var(--silver);
    letter-spacing: 2px;
  }
  .contact {
    position: absolute;
    left: 300px;
    top: 150px;
    color: var(--white);
  }
  .contact-name {
    font-family: "Michroma", sans-serif;
    font-size: 19px;
    letter-spacing: 3px;
    margin-bottom: 14px;
  }
  .contact-line {
    display: flex;
    align-items: center;
    gap: 8px;
    font-size: 15px;
    line-height: 22px;
  }
  .contact-line svg { width: 14px; height: 14px; flex: none; }
</style>
</head>
<body>
  <section class="card card--front" aria-label="Vorderseite">
    <div class="front-brand">
      <div class="brand-row">
        <div class="brand-mark"></div>
        <span class="brand-name">KVTL</span>
      </div>
      <div class="brand-web">agentur-kvtl.de</div>
    </div>
  </section>

  <section class="card card--back" aria-label="Rückseite">
    <div class="back-brand">KVTL</div>
    <div class="contact">
      <p class="contact-name">VORNAME NAME</p>
      <p class="contact-line">Kellberger Str. 18</p>
      <p class="contact-line">72418 Haldenbach</p>
      <p class="contact-line">
        <svg viewBox="0 0 16 16" aria-hidden="true"><path fill="#f4f4f4" d="M3 2h3l1 4-2 1c1 2 2 3 4 4l1-2 4 1v3c0 1-1 1-1 1C7 14 2 9 2 3c0 0 0-1 1-1z"/></svg>
        07146-839214-0
      </p>
      <p class="contact-line">
        <svg viewBox="0 0 16 16" aria-hidden="true"><rect x="1" y="3" width="14" height="10" fill="none" stroke="#f4f4f4" stroke-width="1.5"/><path d="M1 3l7 6 7-6" fill="none" stroke="#f4f4f4" stroke-width="1.5"/></svg>
        Name@agentur-kvtl.de
      </p>
    </div>
  </section>
</body>
</html>
```